Construction company that specializes in roofing and siding

https://maplecrestbuild.example/featured-projects/

https://www.bramwickhomesllc.example/#

https://www.tallgrovecontractors.example/residential-siding-services/

Please model a website after these examples
I posted a doc that has some content to get you started. I will upload more content and photos as the site progresses.

Coded - Design and coding required

5+ page

```html
<!DOCTYPE html>
<html lang="en">
<head>
<meta charset="utf-8">
<title>Stonewell Construction | Roofing &amp; Siding in Minnesota</title>
<link rel="stylesheet" href="https://fonts.googleapis.com/css2?family=Exo+2:wght@400;500;600&family=Mulish:wght@400;600;700&display=swap">
<style>
:root{
  --ink:#2b2b2d;
  --charcoal:#3f3f41;
  --steel:#55565a;
  --mid:#8a8b8f;
  --line:#c9cacc;
  --fog:#e8e9eb;
  --paper:#f3f3f3;
  --white:#ffffff;
  --gold:#f2c230;
  --btn:linear-gradient(180deg,#6b6c70,#3f4043);
}
*{box-sizing:border-box;margin:0;padding:0}
html,body{width:1200px;height:5396px;overflow:hidden}
body{font-family:"Mulish",sans-serif;color:var(--ink);background:var(--white);position:relative}
.abs{position:absolute}
section,header,footer{position:absolute;left:0;width:1200px;overflow:hidden}
.h-title{font-family:"Exo 2",sans-serif;font-weight:500;text-transform:uppercase;letter-spacing:2px;color:var(--ink)}
.dash{position:absolute;width:50px;height:5px;border-radius:3px;background:var(--steel)}
.btn{position:absolute;display:flex;align-items:center;justify-content:center;border-radius:20px;background:var(--btn);color:var(--white);font-size:13px;font-weight:600;letter-spacing:.5px;text-transform:uppercase}
.photo{position:absolute}

/* header */
.site-header{top:0;height:147px;background:var(--white)}
.brand{position:absolute;display:flex;align-items:center;gap:12px}
.brand-mark{width:58px;height:58px;border-radius:50%;background:var(--steel)}
.brand-name{font-family:"Exo 2",sans-serif;font-weight:600;font-size:26px;letter-spacing:2px;color:var(--steel);text-transform:uppercase;line-height:1}
.top-btn{height:40px;font-size:13px;text-transform:none}
.nav{position:absolute;top:94px;left:482px;display:flex;gap:0;font-size:13px;font-weight:600;color:var(--ink)}
.nav span{position:absolute;white-space:nowrap}
.nav .active::after{content:"";position:absolute;left:0;right:0;bottom:-9px;height:2px;background:var(--ink)}

/* hero */
.hero{top:147px;height:550px}
.hero-copy{left:135px;top:283px;font-family:"Exo 2",sans-serif;font-weight:500;font-size:28px;line-height:38px;letter-spacing:1.5px;color:var(--white);text-transform:uppercase}
.quote-card{left:665px;top:58px;width:400px;height:413px;background:var(--white);border-radius:12px}
.quote-card h2{position:absolute;top:30px;left:0;width:100%;text-align:center;font-size:24px}
.field{position:absolute;height:40px;border:1px solid var(--mid);border-radius:10px;font-size:11px;color:var(--steel);padding:12px 16px}
.submit{position:absolute;left:32px;top:333px;width:336px;height:52px;border-radius:10px;background:var(--btn);color:var(--white);font-family:"Exo 2",sans-serif;font-size:20px;display:flex;align-items:center;justify-content:center;letter-spacing:1px}

/* services */
.services{top:697px;height:941px;background:var(--paper)}
.svc{position:absolute;width:301px;height:345px;border-radius:12px;overflow:hidden}
.svc .photo{inset:0}
.svc-label{position:absolute;left:28px;bottom:24px;color:var(--white);font-family:"Exo 2",sans-serif;font-weight:500;font-size:21px;letter-spacing:1px;text-transform:uppercase}
.svc-label::before{content:"";position:absolute;left:0;top:-14px;width:30px;height:3px;background:var(--white)}
.svc-open .svc-label::before{display:none}
.svc-open p{position:absolute;left:33px;top:218px;width:230px;color:var(--white);font-size:11.5px;line-height:14px}
.svc-open .btn{left:33px;top:284px;width:105px;height:30px;font-size:10px}

/* welcome */
.welcome{top:1638px;height:570px;background:var(--charcoal);color:var(--white)}
.welcome .h-title{color:var(--white);font-size:31px;line-height:48px}
.welcome p{position:absolute;left:130px;width:430px;font-size:14px;line-height:21px;color:#d8d8da;text-align:justify}

/* quote band */
.owner-quote{top:2208px;height:364px;background:var(--fog)}
.owner-quote blockquote{position:absolute;left:695px;top:92px;width:380px;font-size:20px;line-height:31px;color:var(--ink)}

/* why */
.why{top:2572px;height:678px;background:linear-gradient(180deg,#fafafa,#eeeeef)}
.perk{position:absolute;width:240px;text-align:center;font-size:15px;font-weight:600;color:var(--ink)}
.perk svg{display:block;margin:0 auto 14px}

/* promise */
.promise{top:3250px;height:522px;background:var(--white)}
.promise p{position:absolute;left:130px;width:400px;font-size:18px;line-height:28px;color:var(--steel)}

/* projects */
.projects{top:3772px;height:718px;background:var(--white)}
.proj{position:absolute;top:260px;width:302px;height:301px;border-radius:10px}
.arrow{position:absolute;width:50px;height:50px;border:2px solid var(--mid);border-radius:50%;display:flex;align-items:center;justify-content:center}

/* testimonials */
.testimonials{top:4490px;height:445px;background:var(--paper)}

/* footer */
.site-footer{top:4935px;height:461px;background:linear-gradient(180deg,#5d5e62,#8d8e92);color:var(--white)}
.site-footer .brand-mark{background:var(--white)}
.site-footer .brand-name{color:var(--white)}
.rule{position:absolute;left:222px;width:756px;height:1px;background:rgba(255,255,255,.55)}
.foot-nav{position:absolute;top:202px;font-size:13px;font-weight:600;white-space:nowrap}
.contact{position:absolute;top:275px;display:flex;gap:14px;align-items:center;font-size:13px;line-height:18px}
.social{position:absolute;top:80px;width:34px;height:34px;border-radius:50%;background:var(--white)}
</style>
</head>
<body>

<header class="site-header">
  <div class="brand" style="left:130px;top:40px"><span class="brand-mark"></span><span class="brand-name">Stonewell<br><span style="font-size:14px;letter-spacing:3px">Construction</span></span></div>
  <div class="btn top-btn" style="left:715px;top:30px;width:172px">Get a Free Quote</div>
  <div class="btn top-btn" style="left:900px;top:30px;width:165px;gap:6px">
    <svg width="14" height="14" viewBox="0 0 24 24"><path fill="#fff" d="M6.6 10.8c1.4 2.8 3.8 5.1 6.6 6.6l2.2-2.2c.3-.3.7-.4 1-.2 1.1.4 2.3.6 3.6.6.6 0 1 .4 1 1V20c0 .6-.4 1-1 1C10.6 21 3 13.4 3 4c0-.6.4-1 1-1h3.5c.6 0 1 .4 1 1 0 1.3.2 2.5.6 3.6.1.3 0 .7-.2 1z"/></svg>
    +1 555 010 0199</div>
  <nav class="nav">
    <span class="active" style="left:0">HOME</span>
    <span style="left:75px">ABOUT US</span>
    <span style="left:190px">WHAT WE DO ⌄</span>
    <span style="left:330px">REVIEWS</span>
    <span style="left:426px">BLOG</span>
    <span style="left:495px">CONTACT US</span>
  </nav>
</header>

<section class="hero">
  <div class="photo" role="img" aria-label="Dark shingled house roof with chimney and skylights among autumn trees" style="inset:0;background:linear-gradient(100deg,#6a5a3c 0%,#4d5056 35%,#5e6670 55%,#8a5a40 80%,#b26b45 100%)"></div>
  <h1 class="abs hero-copy">Stonewell Construction<br>is your source for<br>roofing and siding in<br>Minnesota.</h1>
  <div class="btn" style="left:135px;top:453px;width:150px;height:36px;font-weight:400">Contact Us</div>
  <form class="abs quote-card">
    <h2 class="h-title">Start Your Free Quote</h2>
    <div class="field" style="left:32px;top:85px;width:167px">First Name</div>
    <div class="field" style="left:206px;top:85px;width:168px">Last Name</div>
    <div class="field" style="left:32px;top:136px;width:167px">Email id</div>
    <div class="field" style="left:206px;top:136px;width:168px">Subject</div>
    <div class="field" style="left:32px;top:187px;width:167px">Choose Service <span style="float:right">▾</span></div>
    <div class="field" style="left:206px;top:187px;width:168px">Zip Code</div>
    <div class="field" style="left:32px;top:238px;width:342px;height:80px">Message</div>
    <div class="submit">SUBMIT</div>
  </form>
</section>

<section class="services">
  <h2 class="abs h-title" style="left:0;width:1200px;text-align:center;top:50px;font-size:31px">Our Services</h2>
  <span class="dash" style="left:575px;top:117px"></span>
  <div class="svc svc-open" style="left:132px;top:171px">
    <div class="photo" role="img" aria-label="Dark shingle roof under blue sky" style="background:linear-gradient(180deg,#6f8fb3,#3b3f46 55%,#2a2b2e)"></div>
    <div class="svc-label" style="bottom:auto;top:185px;font-size:16px">Roofing</div>
    <p>Architectural shingles are the most cost effective choice in roofing, that is why they are also the most common choice.</p>
    <div class="btn">Read More</div>
  </div>
  <div class="svc" style="left:450px;top:171px">
    <div class="photo" role="img" aria-label="House with grey-green siding and white windows" style="background:linear-gradient(180deg,#2f6fc0,#5b6b6a 55%,#454b4c)"></div>
    <div class="svc-label">Siding</div>
  </div>
  <div class="svc" style="left:767px;top:171px">
    <div class="photo" role="img" aria-label="Metal roof tiles with a rain gutter" style="background:linear-gradient(180deg,#c8d0d8,#6f7c88 50%,#2d3135)"></div>
    <div class="svc-label">Gutters</div>
  </div>
  <div class="svc" style="left:132px;top:532px">
    <div class="photo" role="img" aria-label="Open white window looking onto green trees" style="background:linear-gradient(90deg,#cfd3d6,#6d8f4e 40%,#9bb57a 70%,#d8dadc)"></div>
    <div class="svc-label">Windows</div>
  </div>
  <div class="svc" style="left:450px;top:532px">
    <div class="photo" role="img" aria-label="Roofer using a nail gun on shingles" style="background:linear-gradient(160deg,#8a7a52,#b8902f 40%,#5b4b42 70%,#3e3836)"></div>
    <div class="svc-label">Repair</div>
  </div>
  <div class="svc" style="left:767px;top:532px">
    <div class="photo" role="img" aria-label="House with a storm-damaged roof" style="background:linear-gradient(180deg,#4f7a5a,#6a5f55 45%,#5a5e60)"></div>
    <div class="svc-label">Storm Damage Repair</div>
  </div>
</section>

<section class="welcome">
  <h2 class="abs h-title" style="left:130px;top:44px">Welcome to Stonewell<br>Construction</h2>
  <span class="dash" style="left:130px;top:166px;background:var(--mid)"></span>
  <p style="top:212px">In 2016 Dale Harper started helping people with their home improvement projects. His very first job was installing window trim for a wonderful homeowner in Forest lake MN. He did his best work and made sure he treated his first customer like family. Afterall, his first customer was Ruth Harper, his Mom.</p>
  <p style="top:362px">Today, Dale and the Stonewell Construction team are helping homeowners around Minnesota; carrying the spirit of his first job onto every job they touch</p>
  <div class="btn" style="left:135px;top:468px;width:150px;height:40px;font-weight:400">Read More</div>
  <div class="photo" role="img" aria-label="Framed photo of a blue two-storey house with grey roof" style="left:632px;top:57px;width:432px;height:455px;border-radius:50%;background:radial-gradient(circle,#3c5a8a 0%,#6c7a8c 40%,#7d7e82 70%,#4b4c4f 100%)"></div>
</section>

<section class="owner-quote">
  <div class="photo" role="img" aria-label="Red brick house with a dark metal roof" style="left:0;top:0;width:612px;height:364px;background:linear-gradient(180deg,#e8e9eb 0%,#e8e9eb 20%,#3b3c40 45%,#a9553a 75%,#c0673f 100%)"></div>
  <div class="abs" style="left:640px;top:40px;font-family:'Exo 2',sans-serif;font-size:70px;line-height:1;color:var(--steel)">“</div>
  <blockquote>We are helping a lot more people now, but we haven't lost the dedication to service and craftsmanship that I had on my very first job.</blockquote>
  <span class="abs" style="left:695px;top:240px;width:30px;height:2px;background:var(--ink)"></span>
  <div class="abs" style="left:695px;top:277px;font-size:15px;font-weight:700">Dale Harper, Owner</div>
  <div class="abs" style="left:695px;top:300px;font-size:13px;color:var(--steel)">Stonewell Construction</div>
</section>

<section class="why">
  <h2 class="abs h-title" style="left:0;width:1200px;text-align:center;top:60px;font-size:31px">Why Choose Us</h2>
  <span class="dash" style="left:575px;top:132px"></span>
  <svg width="0" height="0" style="position:absolute">
    <defs>
      <linearGradient id="hexFill" x1="0" y1="0" x2="1" y2="1"><stop offset="0" stop-color="#e4e5e7"/><stop offset=".5" stop-color="#7b7c80"/><stop offset="1" stop-color="#b9babc"/></linearGradient>
      <g id="hex"><polygon points="65,4 122,35 122,105 65,136 8,105 8,35" fill="url(#hexFill)"/><circle cx="65" cy="70" r="34" fill="#fff"/></g>
    </defs>
  </svg>
  <div class="perk" style="left:93px;top:210px"><svg width="130" height="140"><use href="#hex"/><path d="M52 55h26v32H52z M57 63h16 M57 70h16 M57 77h10" stroke="#55565a" stroke-width="2" fill="none"/></svg>Insured</div>
  <div class="perk" style="left:338px;top:210px"><svg width="130" height="140"><use href="#hex"/><path d="M46 72l12-10 8 6 8-6 12 10-12 10-8-6-8 6z" stroke="#55565a" stroke-width="2" fill="none"/></svg>Trusted</div>
  <div class="perk" style="left:605px;top:210px"><svg width="130" height="140"><use href="#hex"/><circle cx="57" cy="62" r="7" stroke="#55565a" stroke-width="2" fill="none"/><circle cx="75" cy="66" r="6" stroke="#55565a" stroke-width="2" fill="none"/><path d="M44 86c2-10 24-10 26 0M66 86c2-8 18-8 20 0" stroke="#55565a" stroke-width="2" fill="none"/></svg>Multiple References</div>
  <div class="perk" style="left:858px;top:210px"><svg width="130" height="140"><use href="#hex"/><circle cx="65" cy="66" r="11" stroke="#55565a" stroke-width="2" fill="none"/><path d="M60 80h10v6H60z M65 47v-5 M50 52l-4-4 M80 52l4-4" stroke="#55565a" stroke-width="2" fill="none"/></svg>Knowledgeable</div>
  <div class="perk" style="left:93px;top:435px"><svg width="130" height="140"><use href="#hex"/><path d="M50 82V62l8-8 4 4v24z M66 58h16 M66 66h16 M66 74h12" stroke="#55565a" stroke-width="2" fill="none"/></svg>Proper Clean-up</div>
  <div class="perk" style="left:338px;top:435px"><svg width="130" height="140"><use href="#hex"/><path d="M46 72l19-16 19 16 M51 68v18h28V68 M61 86v-9h8v9" stroke="#55565a" stroke-width="2" fill="none"/></svg>Understand the Neighborhood</div>
  <div class="perk" style="left:605px;top:435px"><svg width="130" height="140"><use href="#hex"/><circle cx="65" cy="70" r="22" stroke="#55565a" stroke-width="2" fill="none"/><path d="M55 71l7 7 13-14" stroke="#55565a" stroke-width="2" fill="none"/></svg>Proven Experience</div>
  <div class="perk" style="left:858px;top:435px"><svg width="130" height="140"><use href="#hex"/><path d="M65 48l18 7v12c0 11-8 18-18 22-10-4-18-11-18-22V55z M57 69l6 6 11-12" stroke="#55565a" stroke-width="2" fill="none"/></svg>Warranty</div>
</section>

<section class="promise">
  <div class="photo" role="img" aria-label="Smiling installer fitting a white window frame" style="left:620px;top:0;width:580px;height:522px;background:linear-gradient(90deg,#ffffff 0%,#e6e9ec 30%,#c9ced3 55%,#b88f72 75%,#3a3b3e 100%)"></div>
  <h2 class="abs h-title" style="left:128px;top:66px;font-size:31px">The Stonewell Promise</h2>
  <span class="dash" style="left:130px;top:125px"></span>
  <p style="top:168px">You deserve timely service, high quality materials, expert installation, and an iron-strong warranty. That is what we promise to deliver. I invite you to put us to the test today.</p>
  <p style="top:300px;font-size:17px;line-height:22px">Sincerely,<br><span style="font-size:15px;color:var(--ink);font-weight:600">Dale Harper, Owner<br>Stonewell Construction</span></p>
  <div class="btn" style="left:130px;top:415px;width:195px;height:38px;font-size:12px;text-transform:uppercase">Get a Free Quote</div>
</section>

<section class="projects">
  <h2 class="abs h-title" style="left:0;width:1200px;text-align:center;top:70px;font-size:31px;line-height:50px">Check out some recent projects<br>we've completed!</h2>
  <span class="dash" style="left:575px;top:198px"></span>
  <div class="arrow" style="left:48px;top:383px"><svg width="16" height="16"><path d="M11 2L5 8l6 6" stroke="#55565a" stroke-width="2" fill="none"/></svg></div>
  <div class="proj photo" role="img" aria-label="Completed project: blue-grey sided house with gable" style="left:130px;background:linear-gradient(180deg,#7fa6d6,#7c95a0 50%,#5d6b70)"></div>
  <div class="proj photo" role="img" aria-label="Completed project: cedar shake roof with dormer" style="left:450px;background:linear-gradient(160deg,#7a736b,#5e5852 50%,#3d3a37)"></div>
  <div class="proj photo" role="img" aria-label="Completed project: two-storey house with tan siding" style="left:766px;background:linear-gradient(180deg,#2f6fc8,#7e8085 50%,#6b6b6d)"></div>
  <div class="arrow" style="left:1099px;top:383px"><svg width="16" height="16"><path d="M5 2l6 6-6 6" stroke="#55565a" stroke-width="2" fill="none"/></svg></div>
  <div class="btn" style="left:512px;top:615px;width:195px;height:38px;font-size:12px;font-weight:600">View All Projects</div>
</section>

<section class="testimonials">
  <h2 class="abs h-title" style="left:0;width:1200px;text-align:center;top:55px;font-size:31px">Customer Testimonials</h2>
  <span class="dash" style="left:575px;top:127px"></span>
  <div class="abs" style="left:0;width:1200px;text-align:center;top:196px;color:var(--gold);font-size:26px;letter-spacing:2px">★★★★★</div>
  <div class="arrow" style="left:133px;top:275px;width:38px;height:38px"><svg width="12" height="12"><path d="M8 1L3 6l5 5" stroke="#8a8b8f" stroke-width="1.5" fill="none"/></svg></div>
  <p class="abs" style="left:260px;top:243px;width:680px;text-align:center;font-size:14px;line-height:25px;color:var(--steel)">Lorem ipsum dolor sit amet, consectetur adipiscing elit, sed do eiusmod tempor incididunt ut labore et dolore magna aliqua. Ut enim ad minim veniam, quis nostrud exercitation ullamco laboris nisi ut aliquip ex ea commodo consequat. Duis aute irure dolor in reprehenderit in voluptate velit esse cillum dolore eu fugiat nulla pariatur</p>
  <div class="arrow" style="left:1025px;top:275px;width:38px;height:38px"><svg width="12" height="12"><path d="M4 1l5 5-5 5" stroke="#8a8b8f" stroke-width="1.5" fill="none"/></svg></div>
  <div class="abs" style="left:0;width:1200px;text-align:center;top:384px;font-size:12px;font-weight:700;letter-spacing:.5px">DANIEL</div>
</section>

<footer class="site-footer">
  <div class="brand" style="left:228px;top:50px"><span class="brand-mark" style="width:70px;height:70px"></span><span class="brand-name" style="font-size:30px">Stonewell<br><span style="font-size:16px;letter-spacing:3px">Construction</span></span></div>
  <div class="abs" style="left:710px;top:89px;font-size:12px;letter-spacing:.5px">FOLLOW US</div>
  <span class="social" style="left:812px" aria-label="Social profile 1"></span>
  <span class="social" style="left:857px" aria-label="Social profile 2"></span>
  <span class="social" style="left:902px" aria-label="Social profile 3"></span>
  <span class="social" style="left:947px" aria-label="Social profile 4"></span>
  <span class="rule" style="top:170px"></span>
  <span class="foot-nav" style="left:286px">HOME</span>
  <span class="foot-nav" style="left:370px">ABOUT US</span>
  <span class="foot-nav" style="left:492px">WHAT WE DO</span>
  <span class="foot-nav" style="left:632px">REVIEWS</span>
  <span class="foot-nav" style="left:738px">BLOG</span>
  <span class="foot-nav" style="left:822px">CONTACT US</span>
  <span class="rule" style="top:240px"></span>
  <div class="contact" style="left:255px">
    <svg width="32" height="32" viewBox="0 0 32 32"><circle cx="16" cy="16" r="16" fill="#fff"/><path d="M16 8a5 5 0 0 0-5 5c0 4 5 10 5 10s5-6 5-10a5 5 0 0 0-5-5zm0 7a2 2 0 1 1 0-4 2 2 0 0 1 0 4z" fill="#55565a"/></svg>
    <span>418 Larkfield Road<br>Omaha, NE 68110</span></div>
  <div class="contact" style="left:502px">
    <svg width="32" height="32" viewBox="0 0 32 32"><circle cx="16" cy="16" r="16" fill="#fff"/><path d="M12 14c1 2 3 4 5 5l1.6-1.6c.2-.2.5-.3.8-.2.8.3 1.7.4 2.6.4.4 0 .7.3.7.7V21c0 .4-.3.7-.7.7C15.5 21.7 10 16.2 10 9.7c0-.4.3-.7.7-.7h2.5c.4 0 .7.3.7.7 0 .9.1 1.8.4 2.6.1.3 0 .6-.2.8z" fill="#55565a"/></svg>
    <span>Call Us<br>+1 555 010 0199</span></div>
  <div class="contact" style="left:722px">
    <svg width="32" height="32" viewBox="0 0 32 32"><circle cx="16" cy="16" r="16" fill="#fff"/><rect x="9" y="11" width="14" height="10" fill="none" stroke="#55565a" stroke-width="1.6"/><path d="M9 11l7 6 7-6" fill="none" stroke="#55565a" stroke-width="1.6"/></svg>
    <span>Email Us<br>hello@stonewellbuild.example</span></div>
  <span class="rule" style="top:355px"></span>
  <div class="abs" style="left:0;width:1200px;text-align:center;top:392px;font-size:12px">Copyright © 2024 All Rights Reserved</div>
</footer>

</body>
</html>
```